Casa Morellina Togo Menu seperated in categories

new to go menu for italian restaurant with menu descriptions and prices i like the cover first page to have all the restaurant information, the other pages should be separated in the menu categories, and if we can include a map with the location of the restaurant
Casa Morellina
42 Route 83 S
North Myrtle Beach, SC 29582
open 7 days a week 4-10
Happy hour served Daily at the Bar 4-7
www.casamorellina.com
casamorellinadine@maildrop.example

Restaurant

Sans Serif

Must have
• Prices and pictures and restaurant information

```html
<!DOCTYPE html>
<html lang="en">
<head>
<meta charset="utf-8">
<title>Casa Morellina — Antipasti &amp; Insalata</title>
<link rel="stylesheet" href="https://fonts.googleapis.com/css2?family=Oswald:wght@400;500&family=Open+Sans:wght@400&display=swap">
<style>
  :root {
    --page: #ffffff;
    --ink: #1d1d1d;
    --accent: #9e2330;
    --photo-warm: #c9b07a;
    --photo-deep: #7a4a2a;
  }
  * { margin: 0; padding: 0; box-sizing: border-box; }
  html, body { width: 667px; height: 1200px; overflow: hidden; background: var(--page); }
  .menu-page {
    position: relative;
    width: 667px;
    height: 1200px;
    background: var(--page);
    color: var(--ink);
    font-family: "Open Sans", Arial, sans-serif;
  }
  .page-frame {
    position: absolute;
    left: 40px; top: 40px;
    width: 588px; height: 1121px;
    border: 2px solid var(--accent);
  }
  .section-title {
    position: absolute;
    font-family: "Oswald", "Arial Narrow", sans-serif;
    font-weight: 500;
    font-size: 62px;
    color: var(--ink);
    line-height: 1;
    white-space: nowrap;
    transform-origin: left top;
    transform: scaleX(0.93);
  }
  .title-antipasti { left: 70px; top: 100px; }
  .title-insalata { left: 70px; top: 757px; }
  .dish-photo { position: absolute; }
  .photo-antipasti {
    left: 350px; top: 40px; width: 278px; height: 140px;
    border-radius: 0 0 0 140px / 0 0 0 110px;
    background: radial-gradient(ellipse at 55% 35%, #5f8a34 0%, #b5452f 18%, var(--photo-warm) 42%, #efe6cf 70%, #faf6ec 100%);
  }
  .photo-insalata {
    left: 439px; top: 721px; width: 162px; height: 112px;
    background: radial-gradient(ellipse at 50% 50%, #b5452f 0%, #5a6e2e 28%, #d9d4c8 60%, var(--photo-deep) 100%);
  }
  .add-ons {
    position: absolute; left: 299px; top: 768px;
    font-size: 14px; line-height: 26px;
  }
  .add-ons .price { font-size: 19px; margin-left: 6px; }
  .dish { position: absolute; left: 70px; width: 520px; }
  .dish-head {
    display: flex; align-items: baseline;
    font-family: "Oswald", "Arial Narrow", sans-serif;
    line-height: 22px;
  }
  .dish-name { font-size: 20px; font-weight: 500; color: var(--ink); white-space: nowrap; }
  .leader {
    flex: 1; margin: 0 6px;
    border-bottom: 1.5px dashed var(--accent);
    transform: translateY(-6px);
  }
  .price {
    font-family: "Oswald", "Arial Narrow", sans-serif;
    font-size: 20px; color: var(--accent);
  }
  .dish-desc { font-size: 13.6px; line-height: 17px; }
</style>
</head>
<body>
<main class="menu-page">
  <div class="page-frame"></div>

  <div class="dish-photo photo-antipasti" role="img" aria-label="Plated antipasto with roasted peppers, basil and balsamic drizzle"></div>
  <h1 class="section-title title-antipasti">ANTIPASTI</h1>

  <section class="dish" style="top:187px">
    <div class="dish-head"><span class="dish-name">Mozzarella Completa</span><span class="leader"></span><span class="price">9.95</span></div>
    <p class="dish-desc">Mozzarella, Roasted Red Peppers, Ricotta Cheese, Fresh Tomatoes, Prosciutto Di Parma, Drizzled with Evoo &amp; Aged Balsamic</p>
  </section>
  <section class="dish" style="top:269px">
    <div class="dish-head"><span class="dish-name">Fried Calamari</span><span class="leader"></span><span class="price">8.95</span></div>
    <p class="dish-desc">Calamari Lightly Breaded, Fried to Perfection, Served with Homemade Spicy Marinara Sauce</p>
  </section>
  <section class="dish" style="top:351px">
    <div class="dish-head"><span class="dish-name">Escargot</span><span class="leader"></span><span class="price">9.95</span></div>
    <p class="dish-desc">Escargot in a Creamy Gorgonzola Cheese Sauce, Garlic, Sundried Tomatoes, Baked to Perfection</p>
  </section>
  <section class="dish" style="top:433px">
    <div class="dish-head"><span class="dish-name">Zuppa Di Cozze</span><span class="leader"></span><span class="price">8.95</span></div>
    <p class="dish-desc">Fresh PEI Mussels in a choice of Marinara or Lemon Fusion Sauce</p>
  </section>
  <section class="dish" style="top:497px">
    <div class="dish-head"><span class="dish-name">Mozzarella Caprese</span><span class="leader"></span><span class="price">8.95</span></div>
    <p class="dish-desc">Fresh Tomato, Homemade Mozzarella, Fresh Basil, Roasted Red Peppers, Evoo and Balsamic</p>
  </section>
  <section class="dish" style="top:580px">
    <div class="dish-head"><span class="dish-name">Shrimp Florentine</span><span class="leader"></span><span class="price">11.95</span></div>
    <p class="dish-desc">Jumbo Shrimp wrapped in Prosciutto, in a Lemon Infusion Sauce, served over Spinach</p>
  </section>
  <section class="dish" style="top:662px">
    <div class="dish-head"><span class="dish-name">Clams Oreganata</span><span class="leader"></span><span class="price">8.95</span></div>
    <p class="dish-desc">Fresh Little Neck Clams topped with Italian Seasoned Bred Crumbs and Baked to Perfection</p>
  </section>

  <h2 class="section-title title-insalata">INSALATA</h2>
  <div class="add-ons">
    <div>Add Chicken <span class="price">3.95</span></div>
    <div>Add Shrimp <span class="price">5.95</span></div>
  </div>
  <div class="dish-photo photo-insalata" role="img" aria-label="Salad with mixed greens, red onions and shaved cheese"></div>

  <section class="dish" style="top:842px">
    <div class="dish-head"><span class="dish-name">Italian Salad</span><span class="leader"></span><span class="price">8.95</span></div>
    <p class="dish-desc">Fresh Mixed Greens, Tomatoes, Cucumbers, Onions, Mozzarella, Banana Peppers, tossed in our homemade Italian Dressing</p>
  </section>
  <section class="dish" style="top:921px">
    <div class="dish-head"><span class="dish-name">Insalata Gorgonzola</span><span class="leader"></span><span class="price">9.95</span></div>
    <p class="dish-desc">Fresh Romaine Lettuce, Gorgonzola, thin sliced Pear, Red Onions, Walnuts, in our homemade Italian Dressing</p>
  </section>
  <section class="dish" style="top:1002px">
    <div class="dish-head"><span class="dish-name">Greek Salad</span><span class="leader"></span><span class="price">8.95</span></div>
    <p class="dish-desc">Mixed Greens, Tomatoes, Cucumbers, Red Onions, Bell Peppers, Kalamata Olives and Feta Cheese in our homemade Italian Dressing</p>
  </section>
  <section class="dish" style="top:1084px">
    <div class="dish-head"><span class="dish-name">Caesar Salad</span><span class="leader"></span><span class="price">7.95</span></div>
    <p class="dish-desc">Fresh Romaine Tossed with Caesar Dressing, Croutons, topped with Parmesan Cheese</p>
  </section>
</main>
</body>
</html>
```